Business Card design for insurance broker in Denver, CO, USA

I need a business card designed using this logo that was just created. We sell life and disability income insurance to US consumers.
Looking for a professionally designed card to make use of the logo and have something to hand to prospects or new business referral sources. The card could be white, gray, black or whatever you would recommend.

Target Market(s)

US Consumers and other financial professionals that I partner with.

Industry/Entity Type

Insurance Broker

Contact Information for Business Card

Owen T. Farrow, CLU, LUTCF (please note that CLU should have a superscript R in a circle for registered trademark)
President
phone (555) 555-0187
email owen@keelbrookcover.example
4620 W. Halvern Rd, Suite 300, Larkmoor Village, CO 80999
Somewhere fit in a tagline saying "Your resource for life, long term care, and disability insurance" (maybe the back if it doesn't fit on the front, your call)

Font styles to use
Sans Serif

Requirements
Must have
• Must have logo in correct blue and gray colors, my name, address, phone, email. Order and placement determined by the designer.
• I just want something that looks a more professional than what I could have done using the business card designer tool on pixelbazaar.example or QuillPress, or any other do-it-yourself tool
• A regular rectangular business card with square corners is preferred
Nice to have
• I included the logos of 2 organizations I belong to (GKLS and WOBCE). They should be small, but visible on the back only. If it doesn’t look good, this is not a requirement, feel free to drop it.
Should not have
• Do not add any colors not already in the logo, except use of black and whites which are okay. If you use the logo on the back and want to make that in all black, gray or white, that may be okay as well.

```html
<!DOCTYPE html>
<html lang="en">
<head>
<meta charset="utf-8">
<title>Keelbrook Cover — Business Card</title>
<link rel="stylesheet" href="https://fonts.googleapis.com/css2?family=Montserrat:wght@400;500;600;700&display=swap">
<style>
  :root{
    --brand-blue:#1e88d2;
    --brand-gray:#8a8d91;
    --ink:#1e1e1e;
    --paper:#f6f6f6;
    --stage:#e4e2de;
    --white:#ffffff;
  }
  *{box-sizing:border-box;margin:0;padding:0}
  html,body{width:1200px;height:834px;overflow:hidden}
  body{
    background:var(--stage);
    font-family:"Montserrat",Arial,sans-serif;
    display:flex;align-items:center;justify-content:center;gap:40px;
  }
  .card{
    position:relative;width:540px;height:309px;overflow:hidden;
    box-shadow:0 6px 18px rgba(0,0,0,.18);
  }
  .card-band{position:absolute;inset:0;width:100%;height:100%}

  /* Front */
  .card--front{background:var(--paper);color:var(--ink)}
  .contact{position:absolute;left:38px;top:34px}
  .contact-name{font-size:17px;font-weight:700;letter-spacing:.2px}
  .contact-name sup{font-size:9px;font-weight:600}
  .contact-title{font-size:9px;font-weight:500;letter-spacing:4px;color:var(--brand-blue);margin-top:4px}
  .contact-list{list-style:none;margin-top:20px}
  .contact-list li{display:flex;align-items:flex-start;gap:9px;font-size:10.5px;font-weight:500;line-height:1.35;margin-bottom:7px}
  .contact-icon{flex:0 0 15px;width:15px;height:15px;border-radius:50%;background:var(--brand-blue);display:flex;align-items:center;justify-content:center}
  .contact-icon svg{width:9px;height:9px}

  .brand{display:flex;align-items:center;gap:9px}
  .brand-dot{width:30px;height:30px;border-radius:50%;border:3px solid var(--brand-blue)}
  .brand-name{font-weight:600;color:var(--brand-blue);text-transform:uppercase;letter-spacing:1.5px;line-height:1.05}
  .card--front .brand{position:absolute;right:40px;top:128px}
  .card--front .brand-name{font-size:17px}

  /* Back */
  .card--back{background:var(--ink);color:var(--white)}
  .card--back .brand{position:absolute;left:0;right:0;top:78px;justify-content:center}
  .card--back .brand-dot{width:40px;height:40px;border-width:4px}
  .card--back .brand-name{font-size:24px}
  .tagline{position:absolute;left:0;right:0;top:148px;text-align:center;font-size:7.5px;font-weight:600;letter-spacing:1.6px;text-transform:uppercase;color:var(--white)}
  .badges{position:absolute;left:70px;bottom:22px;display:flex;gap:22px}
  .badge{width:30px;height:30px;border-radius:50%;background:#c9ccd0}
  .badge--square{border-radius:3px;background:#b8c2cc}
</style>
</head>
<body>

  <section class="card card--front" aria-label="Card front">
    <svg class="card-band" viewBox="0 0 540 309" preserveAspectRatio="none" aria-hidden="true">
      <polygon points="0,232 540,258 540,309 0,309" fill="#1e1e1e"/>
      <polygon points="0,222 540,248 540,252 0,226" fill="#1e88d2"/>
      <polygon points="0,214 540,240 540,242 0,216" fill="#8a8d91"/>
    </svg>

    <div class="contact">
      <p class="contact-name">Owen T. Farrow, CLU<sup>®</sup>, LUTCF</p>
      <p class="contact-title">PRESIDENT</p>
      <ul class="contact-list">
        <li><span class="contact-icon"><svg viewBox="0 0 10 10"><path d="M2 1l2 2-1 1.2c.6 1.2 1.6 2.2 2.8 2.8L7 6l2 2-1.2 1.2C4.5 9 1 5.5.8 2.2z" fill="#fff"/></svg></span>(555) 555-0187</li>
        <li><span class="contact-icon"><svg viewBox="0 0 10 10"><rect x="1" y="2.5" width="8" height="5.5" fill="none" stroke="#fff" stroke-width="1"/><path d="M1 2.5l4 3 4-3" fill="none" stroke="#fff" stroke-width="1"/></svg></span>owen@keelbrookcover.example</li>
        <li><span class="contact-icon"><svg viewBox="0 0 10 10"><path d="M5 .8a3 3 0 0 1 3 3c0 2.2-3 5.4-3 5.4S2 6 2 3.8a3 3 0 0 1 3-3z" fill="#fff"/><circle cx="5" cy="3.8" r="1" fill="#1e88d2"/></svg></span><span>4620 W. Halvern Rd, Suite 300,<br>Larkmoor Village, CO 80999</span></li>
      </ul>
    </div>

    <div class="brand">
      <span class="brand-dot"></span>
      <span class="brand-name">Keelbrook<br>Cover</span>
    </div>
  </section>

  <section class="card card--back" aria-label="Card back">
    <svg class="card-band" viewBox="0 0 540 309" preserveAspectRatio="none" aria-hidden="true">
      <polygon points="0,196 540,248 540,309 0,309" fill="#f6f6f6"/>
      <polygon points="0,186 540,238 540,243 0,191" fill="#1e88d2"/>
      <polygon points="0,178 540,230 540,232 0,180" fill="#8a8d91"/>
    </svg>

    <div class="brand">
      <span class="brand-dot"></span>
      <span class="brand-name">Keelbrook Cover</span>
    </div>
    <p class="tagline">Your resource for life, long term care and disability insurance</p>

    <div class="badges">
      <span class="badge" role="img" aria-label="Member organization badge"></span>
      <span class="badge badge--square" role="img" aria-label="Member organization badge"></span>
    </div>
  </section>

</body>
</html>
```